Wholesale in Gold Jewellery & Gold Bullion

We are an established gold jewellery and gold bullion wholesaler selling these products to international clients. We already have a name and logo of our company, hence please view attached current card design. We need a completely new design to compliment our business and industry and the final design should be new and elegant.

Contact Information for Business Card

New card details must be same as per current card. Like logo, name, tel no. & etc.

Colors

Designer to choose colors to be used in the design.

```html
<!DOCTYPE html>
<html lang="en">
<head>
<meta charset="utf-8">
<title>Suresh &amp; Co – Business Card</title>
<link rel="stylesheet" href="https://fonts.googleapis.com/css2?family=Montserrat:wght@400;600;700&display=swap">
<style>
  :root {
    --backdrop: #cfcfcf;
    --card: #ffffff;
    --ink: #3d3d3d;
    --ink-soft: #4a4a4a;
    --gold: #d98f17;
    --brand-ink: #1e1a18;
  }
  * { margin: 0; padding: 0; box-sizing: border-box; }
  html, body {
    width: 1200px; height: 800px; overflow: hidden;
    background: var(--backdrop);
    font-family: "Montserrat", sans-serif;
  }
  .business-card {
    position: absolute; left: 75px; top: 100px;
    width: 1050px; height: 600px;
    background: var(--card);
    box-shadow: 0 10px 30px rgba(0,0,0,0.18);
  }
  .accent-bar {
    position: absolute; left: 0; top: 50px;
    width: 38px; height: 62px;
    background: var(--gold);
  }
  .identity { position: absolute; left: 66px; top: 52px; }
  .person-name {
    font-weight: 700; font-size: 36px; color: var(--ink);
    letter-spacing: 0.5px; line-height: 1.1;
  }
  .person-role {
    font-weight: 400; font-size: 26px; color: var(--gold);
    line-height: 1.1; margin-top: -2px;
  }
  .contact-block {
    position: absolute; left: 60px; top: 330px;
    font-size: 22px; color: var(--ink-soft); letter-spacing: 0.6px;
  }
  .address { margin-left: 52px; line-height: 30px; margin-bottom: 10px; }
  .contact-line { display: flex; align-items: center; height: 34px; }
  .contact-icon { width: 28px; height: 24px; margin-right: 24px; flex: none; }
  .brand {
    position: absolute; right: 60px; bottom: 56px;
    display: flex; align-items: center; gap: 18px;
  }
  .brand-dot {
    width: 58px; height: 58px; border-radius: 50%;
    background: var(--gold);
  }
  .brand-name {
    font-weight: 700; font-size: 32px; color: var(--brand-ink);
    letter-spacing: 1px;
  }
</style>
</head>
<body>
  <main class="business-card">
    <div class="accent-bar"></div>

    <header class="identity">
      <h1 class="person-name">Ravindra Kothapalli</h1>
      <p class="person-role">Director</p>
    </header>

    <section class="contact-block">
      <p class="address">52 Lower Kerr Ln,<br>Singapore 208815</p>

      <p class="contact-line">
        <svg class="contact-icon" viewBox="0 0 28 24" aria-hidden="true">
          <rect x="8" y="1" width="12" height="22" rx="2" fill="none" stroke="var(--gold)" stroke-width="2"/>
          <line x1="12" y1="19" x2="16" y2="19" stroke="var(--gold)" stroke-width="2"/>
        </svg>
        +65 9123 4567
      </p>

      <p class="contact-line">
        <svg class="contact-icon" viewBox="0 0 28 24" aria-hidden="true">
          <path d="M9 2 L13 2 L14 7 L11 9 Q13 15 18 17 L20 14 L25 15 L25 19 Q24 23 19 22 Q7 18 5 6 Q5 2 9 2 Z" fill="var(--gold)"/>
        </svg>
        +65 6100 2200
      </p>

      <p class="contact-line">
        <svg class="contact-icon" viewBox="0 0 28 24" aria-hidden="true">
          <rect x="8" y="1" width="12" height="8" fill="none" stroke="var(--gold)" stroke-width="2"/>
          <rect x="3" y="9" width="22" height="13" rx="2" fill="var(--gold)"/>
          <rect x="8" y="14" width="12" height="4" fill="#fff"/>
        </svg>
        +65 6200 3300
      </p>

      <p class="contact-line">
        <svg class="contact-icon" viewBox="0 0 28 24" aria-hidden="true">
          <rect x="2" y="5" width="24" height="15" fill="var(--gold)"/>
          <path d="M2 5 L14 14 L26 5" fill="none" stroke="#fff" stroke-width="1.6"/>
        </svg>
        ravindra@sureshco.com
      </p>
    </section>

    <div class="brand">
      <span class="brand-dot"></span>
      <span class="brand-name">SURESH &amp; CO PTE LTD</span>
    </div>
  </main>
</body>
</html>
```